RQV Wellness Co Business Card for food and Beverage Wizards & Alchemists

One main business card design for a wellness enterprise which represents two brands. We need one primary card design, for two different employees. The only difference between the cards will be the name, title and phone number for each employee, all other design elements will be same.
I've uploaded the logos for each brand. I have also uploaded a mockup which I made using Google's drawing tool. I can provide example images of business cards we find attractive if you would like some help picturing what we like.
I'm picturing the color splash on the back of the card below the two logos to be a dark burgundy or blue. This may sound a bit silly but the feel of the card and color should look almost like wizard dress robes. Dark emerald green, dark blue and dark burgundy with black undertones and gold lace.

Reason: Thank you all for the submissions. I will need some extra time to give you feedback. Cheers

Target Market(s)

Healthy food and beverage industry

Industry/Entity Type

Health And Wellness

Contact Information for Business Card

On one side we would like the business name, location, title of employee, employee name and contact details. On the flip side we would like our two brand logos and a splash of color. We would like the card to have a black font with some gold accents if possible. We would also like the trim of the business card or a middle ply within the card stock to have a color other than white.

Font styles to use
Serif

Colors
ec1f27
0255a3
00a990

Requirements
Must have
• Bold dark colors, happy to provide sample photos of business cards I like from snapgallery. Must have a version for two different employees. Must be sharp, modern and chic.
Nice to have
• Thick card stock layer in between the front and back of card that is either black or gold lace or something to make it feel, well let's say to make it feel expensive.
Should not have
• Should not have any cartoon-ey elements. All business.

```html
<!DOCTYPE html>
<html lang="en">
<head>
<meta charset="utf-8">
<title>RQV Wellness Co – Business Cards</title>
<link rel="stylesheet" href="https://fonts.googleapis.com/css2?family=Lato:ital,wght@0,400;0,700;0,900;1,700&display=swap">
<style>
  :root {
    --page: #ffffff;
    --label: #4a4a4a;
    --gold-light: #f6e39a;
    --gold-mid: #d9b23c;
    --gold-deep: #a97f12;
    --black-card: #221d1b;
    --black-card-2: #2e2724;
    --navy: #2a3170;
    --navy-deep: #141633;
    --rim-blue: #3b6fd1;
    --ink-dark: #141414;
    --ink-light: #ffffff;
  }
  * { box-sizing: border-box; margin: 0; padding: 0; }
  html, body {
    width: 1200px; height: 1000px; overflow: hidden;
    background: var(--page);
    font-family: "Lato", Arial, sans-serif;
  }
  .sheet { position: relative; width: 1200px; height: 1000px; }
  .option-label {
    position: absolute; top: 50px; width: 224px; text-align: center;
    font-weight: 700; font-size: 14px; letter-spacing: 0.2px; color: var(--label);
  }
  .card {
    position: absolute; width: 224px; height: 391px; overflow: hidden;
    text-align: center;
  }
  .card--gold {
    background: linear-gradient(90deg, var(--gold-deep) 0%, var(--gold-mid) 18%, var(--gold-light) 48%, var(--gold-mid) 78%, var(--gold-deep) 100%);
    color: var(--ink-dark);
  }
  .card--black {
    background: linear-gradient(120deg, var(--black-card) 0%, var(--black-card-2) 50%, var(--black-card) 100%);
    color: var(--ink-light);
  }
  .card__wave { position: absolute; left: 0; top: 0; width: 224px; height: 391px; }
  .card__company { position: absolute; top: 44px; width: 100%; font-weight: 700; font-size: 15px; }
  .card__city { position: absolute; top: 70px; width: 100%; font-size: 13px; }
  .card__rule {
    position: absolute; left: 63px; width: 98px; height: 2px; background: var(--ink-dark);
  }
  .card--black .card__rule {
    background: linear-gradient(90deg, var(--gold-deep), var(--gold-light), var(--gold-deep));
  }
  .card__rule--top { top: 115px; }
  .card__rule--bottom { top: 176px; }
  .card__name { position: absolute; top: 126px; width: 100%; font-weight: 900; font-size: 17px; }
  .card__title { position: absolute; top: 152px; width: 100%; font-style: italic; font-weight: 700; font-size: 11px; }
  .card__contact {
    position: absolute; width: 100%; font-size: 12.5px;
    display: flex; justify-content: center; align-items: center; gap: 6px;
  }
  .card__contact--phone { top: 199px; font-size: 13.5px; }
  .card__contact--email { top: 223px; font-size: 12px; gap: 8px; }
  .icon { width: 11px; height: 11px; flex: none; }
  .icon--mail { width: 13px; height: 9px; }
  .card--gold .icon { fill: var(--ink-dark); }
  .card--black .icon { fill: var(--gold-mid); }
  .brand-mark {
    position: absolute; width: 100%; display: flex; justify-content: center; align-items: center; gap: 8px;
    font-weight: 900; font-size: 17px; color: var(--ink-dark);
  }
  .brand-mark__dot { width: 12px; height: 12px; border-radius: 50%; background: var(--ink-dark); }
  .brand-mark--tonics { top: 70px; }
  .brand-mark--guild { top: 175px; }
</style>
</head>
<body>
<svg width="0" height="0" style="position:absolute">
  <defs>
    <linearGradient id="rimGold" x1="0" y1="0" x2="1" y2="0">
      <stop offset="0" stop-color="#a97f12"/>
      <stop offset="0.5" stop-color="#f6e39a"/>
      <stop offset="1" stop-color="#c99a2a"/>
    </linearGradient>
    <linearGradient id="robeBlue" x1="0" y1="0" x2="0.3" y2="1">
      <stop offset="0" stop-color="#323a86"/>
      <stop offset="0.55" stop-color="#2a3170"/>
      <stop offset="1" stop-color="#121218"/>
    </linearGradient>
    <symbol id="wave" viewBox="0 0 224 391">
      <path d="M0,312 C55,318 95,302 128,282 C160,262 192,254 224,250 L224,391 L0,391 Z" fill="url(#rimGold)"/>
      <path d="M0,322 C55,326 98,308 132,290 C165,270 195,260 224,258 L224,391 L0,391 Z" fill="#3b6fd1"/>
      <path d="M0,324 C55,328 98,311 132,293 C165,273 195,263 224,261 L224,391 L0,391 Z" fill="url(#robeBlue)"/>
    </symbol>
    <symbol id="phone" viewBox="0 0 24 24">
      <path d="M6.6 10.8a15.1 15.1 0 0 0 6.6 6.6l2.2-2.2a1 1 0 0 1 1-.25 11.4 11.4 0 0 0 3.6.57 1 1 0 0 1 1 1V20a1 1 0 0 1-1 1A17 17 0 0 1 3 4a1 1 0 0 1 1-1h3.5a1 1 0 0 1 1 1c0 1.25.2 2.45.57 3.6a1 1 0 0 1-.25 1z"/>
    </symbol>
    <symbol id="mail" viewBox="0 0 26 18">
      <path d="M0 0h26v18H0z M2 2l11 8 11-8v-0.5H2z" fill-rule="evenodd"/>
    </symbol>
  </defs>
</svg>

<main class="sheet">
  <div class="option-label" style="left:491px">OPTION GOLD</div>
  <div class="option-label" style="left:796px">OPTION BLACK</div>

  <!-- Row 1 -->
  <section class="card card--gold card--back" style="left:181px; top:85px">
    <div class="brand-mark brand-mark--tonics"><span class="brand-mark__dot"></span>Alder Tonics</div>
    <div class="brand-mark brand-mark--guild">Ember Guild</div>
    <svg class="card__wave"><use href="#wave"/></svg>
  </section>

  <section class="card card--gold" style="left:491px; top:85px">
    <div class="card__company">RQV Wellness Co</div>
    <div class="card__city">Vinehaven, CA</div>
    <div class="card__rule card__rule--top"></div>
    <div class="card__name">Dana Rowley</div>
    <div class="card__title">Beverage Alchemist</div>
    <div class="card__rule card__rule--bottom"></div>
    <div class="card__contact card__contact--phone"><svg class="icon"><use href="#phone"/></svg>415.555.0142</div>
    <div class="card__contact card__contact--email"><svg class="icon icon--mail"><use href="#mail"/></svg>rqvwellnessco@mail.com</div>
    <svg class="card__wave"><use href="#wave"/></svg>
  </section>

  <section class="card card--black" style="left:796px; top:85px">
    <div class="card__company">RQV Wellness Co</div>
    <div class="card__city">Vinehaven, CA</div>
    <div class="card__rule card__rule--top"></div>
    <div class="card__name">Dana Rowley</div>
    <div class="card__title">Beverage Alchemist</div>
    <div class="card__rule card__rule--bottom"></div>
    <div class="card__contact card__contact--phone"><svg class="icon"><use href="#phone"/></svg>415.555.0142</div>
    <div class="card__contact card__contact--email"><svg class="icon icon--mail"><use href="#mail"/></svg>rqvwellnessco@mail.com</div>
    <svg class="card__wave"><use href="#wave"/></svg>
  </section>

  <!-- Row 2 -->
  <section class="card card--gold card--back" style="left:181px; top:548px">
    <div class="brand-mark brand-mark--tonics"><span class="brand-mark__dot"></span>Alder Tonics</div>
    <div class="brand-mark brand-mark--guild">Ember Guild</div>
    <svg class="card__wave"><use href="#wave"/></svg>
  </section>

  <section class="card card--gold" style="left:491px; top:548px">
    <div class="card__company">RQV Wellness Co</div>
    <div class="card__city">Vinehaven, CA</div>
    <div class="card__rule card__rule--top"></div>
    <div class="card__name">Martin Hallewell</div>
    <div class="card__title">Cookie Wizard</div>
    <div class="card__rule card__rule--bottom"></div>
    <div class="card__contact card__contact--phone"><svg class="icon"><use href="#phone"/></svg>510.555.0187</div>
    <div class="card__contact card__contact--email"><svg class="icon icon--mail"><use href="#mail"/></svg>rqvwellnessco@mail.com</div>
    <svg class="card__wave"><use href="#wave"/></svg>
  </section>

  <section class="card card--black" style="left:796px; top:548px">
    <div class="card__company">RQV Wellness Co</div>
    <div class="card__city">Vinehaven, CA</div>
    <div class="card__rule card__rule--top"></div>
    <div class="card__name">Martin Hallewell</div>
    <div class="card__title">Cookie Wizard</div>
    <div class="card__rule card__rule--bottom"></div>
    <div class="card__contact card__contact--phone"><svg class="icon"><use href="#phone"/></svg>510.555.0187</div>
    <div class="card__contact card__contact--email"><svg class="icon icon--mail"><use href="#mail"/></svg>rqvwellnessco@mail.com</div>
    <svg class="card__wave"><use href="#wave"/></svg>
  </section>
</main>
</body>
</html>
```